Business Card Design Project

Beam Clinic Hub

Dr Lomen Priscu M.D, F.R.C.S
Vascular and Vein Surgery

47-15 Quillford Avenue, Suite 318
Astoria
NY 11103

212-555-0183
718-555-0146
www.mendorapro.us back of the card for scheduled appointments up to 5 appointment dates

Target Market(s)

Male and Female patients from 25 onwards with spider veins or varicose veins

Industry/Entity Type

Business

Font styles to use
Serif

Colors
86cae6
85abd2
0456a4

Requirements
Must have
• Modern Sophisticated design using light blue and grey text
Should not have
• hearts or flowers

```html
<!DOCTYPE html>
<html lang="en">
<head>
<meta charset="utf-8">
<title>Beam Clinic Hub – Business Card</title>
<link rel="stylesheet" href="https://fonts.googleapis.com/css2?family=Cormorant+Garamond:wght@500;600&family=Playfair+Display:wght@800&family=Lora:wght@400;700&display=swap">
<style>
  :root {
    --page: #eceff1;
    --teal: #5cc4cf;
    --teal-light: #86cae6;
    --blue: #0456a4;
    --blue-bright: #1aa3e8;
    --white: #ffffff;
    --ink: #3a4147;
    --grey: #6b737a;
    --slate: #3b4248;
    --silver-a: #8d949a;
    --silver-b: #f4f6f7;
  }
  * { box-sizing: border-box; margin: 0; padding: 0; }
  html, body { width: 1200px; height: 1050px; overflow: hidden; }
  body { background: var(--page); position: relative; font-family: "Lora", serif; }

  .card {
    position: absolute; top: 88px; width: 500px; height: 875px;
    overflow: hidden; box-shadow: 0 10px 30px rgba(0,0,0,0.18);
  }
  .card--front { left: 60px; background: var(--teal); }
  .card--back { left: 640px; background: var(--white); }

  /* front */
  .front-head { position: absolute; left: 0; top: 0; width: 100%; height: 190px; background: var(--white); }
  .front-head__strip { position: absolute; left: 0; top: 0; width: 100%; height: 10px; background: var(--teal-light); }
  .front-head__line { position: absolute; left: 0; top: 14px; width: 100%; height: 4px; background: var(--blue-bright); }
  .front-head__rule { position: absolute; left: 0; top: 184px; width: 100%; height: 8px; background: var(--blue-bright); }
  .clinic-name {
    position: absolute; left: 0; top: 66px; width: 100%; text-align: center;
    font-family: "Cormorant Garamond", serif; font-weight: 500; font-size: 50px;
    color: var(--teal); letter-spacing: 0.5px;
  }

  .name-box {
    position: absolute; left: 175px; top: 160px; width: 305px; height: 118px;
    background: var(--white); padding: 18px 0 0 20px; color: var(--ink);
  }
  .name-box__name { font-family: "Playfair Display", serif; font-weight: 800; font-size: 25px; line-height: 1; color: #1f1f1f; }
  .name-box__creds { font-size: 14px; margin-top: 10px; padding-left: 4px; color: var(--grey); }
  .name-box__role { font-size: 14px; margin-top: 3px; padding-left: 4px; color: var(--grey); }

  .tree-line { position: absolute; background: var(--white); }
  .tree-line--trunk { left: 68px; top: 230px; width: 2px; height: 384px; }
  .tree-line--top { left: 68px; top: 230px; width: 107px; height: 2px; }
  .tree-line--phone { left: 68px; top: 362px; width: 132px; height: 2px; }
  .tree-line--email { left: 68px; top: 487px; width: 82px; height: 2px; }
  .tree-line--web { left: 68px; top: 612px; width: 42px; height: 2px; }

  .contact-box {
    position: absolute; height: 96px; border: 2px solid var(--white);
    color: var(--white); text-align: center; padding-top: 16px;
  }
  .contact-box__label { font-weight: 700; font-size: 19px; letter-spacing: 1.5px; }
  .contact-box__value { font-size: 16px; margin-top: 6px; }
  .contact-box--phone { left: 200px; top: 315px; width: 270px; padding-top: 10px; }
  .contact-box--phone .contact-box__value { margin-top: 2px; line-height: 1.35; }
  .contact-box--email { left: 150px; top: 440px; width: 290px; }
  .contact-box--web { left: 110px; top: 565px; width: 320px; }

  .front-foot__silver {
    position: absolute; left: 0; top: 760px; width: 100%; height: 8px;
    background: linear-gradient(90deg, var(--silver-a), var(--silver-b) 50%, var(--silver-a));
  }
  .front-foot {
    position: absolute; left: 0; top: 768px; width: 100%; height: 107px; background: var(--blue-bright);
    color: var(--white); font-size: 18px; line-height: 1.5; padding: 26px 0 0 26px;
  }

  /* back */
  .back-shapes { position: absolute; left: 0; top: 0; }
  .appointments { position: absolute; left: 40px; top: 44px; width: 420px; color: var(--ink); }
  .appointments__title {
    font-family: "Cormorant Garamond", serif; font-weight: 600; font-size: 30px;
    color: var(--teal); margin-bottom: 12px;
  }
  .appointments__row {
    display: flex; align-items: flex-end; gap: 10px; height: 38px;
    font-size: 15px; color: var(--grey);
  }
  .appointments__slot { flex: 1; border-bottom: 1px solid #b8c0c6; height: 22px; }
  .back-address {
    position: absolute; left: 40px; top: 600px; color: var(--white);
    font-size: 22px; line-height: 1.6;
  }
</style>
</head>
<body>

<section class="card card--front" aria-label="Card front">
  <div class="front-head">
    <div class="front-head__strip"></div>
    <div class="front-head__line"></div>
    <h1 class="clinic-name">Beam Clinic Hub</h1>
    <div class="front-head__rule"></div>
  </div>

  <div class="tree-line tree-line--trunk"></div>
  <div class="tree-line tree-line--top"></div>
  <div class="tree-line tree-line--phone"></div>
  <div class="tree-line tree-line--email"></div>
  <div class="tree-line tree-line--web"></div>

  <div class="name-box">
    <p class="name-box__name">Dr Lomen Priscu</p>
    <p class="name-box__creds">M.D, F.R.C.S</p>
    <p class="name-box__role">Vascular and Vein Surgery</p>
  </div>

  <div class="contact-box contact-box--phone">
    <p class="contact-box__label">PHONE</p>
    <p class="contact-box__value">212-555-0183<br>718-555-0146</p>
  </div>
  <div class="contact-box contact-box--email">
    <p class="contact-box__label">EMAIL</p>
    <p class="contact-box__value">info@mendorapro.us</p>
  </div>
  <div class="contact-box contact-box--web">
    <p class="contact-box__label">WEBSITE</p>
    <p class="contact-box__value">www.mendorapro.us</p>
  </div>

  <div class="front-foot__silver"></div>
  <p class="front-foot">47-15 Quillford Avenue, Suite 318<br>Astoria NY 11103</p>
</section>

<section class="card card--back" aria-label="Card back">
  <svg class="back-shapes" width="500" height="875" viewBox="0 0 500 875">
    <polygon points="0,0 500,0 500,10 0,10" fill="var(--teal-light)"/>
    <polygon points="0,14 500,14 500,18 0,18" fill="var(--blue-bright)"/>
    <polygon points="0,430 500,320 500,350 0,460" fill="var(--slate)"/>
    <polygon points="0,460 500,350 500,875 0,875" fill="var(--teal)"/>
  </svg>

  <div class="appointments">
    <h2 class="appointments__title">Your Appointments</h2>
    <div class="appointments__row">Date<span class="appointments__slot"></span>Time<span class="appointments__slot"></span></div>
    <div class="appointments__row">Date<span class="appointments__slot"></span>Time<span class="appointments__slot"></span></div>
    <div class="appointments__row">Date<span class="appointments__slot"></span>Time<span class="appointments__slot"></span></div>
    <div class="appointments__row">Date<span class="appointments__slot"></span>Time<span class="appointments__slot"></span></div>
    <div class="appointments__row">Date<span class="appointments__slot"></span>Time<span class="appointments__slot"></span></div>
  </div>

  <p class="back-address">47-15 Quillford Avenue, Suite 318<br>Astoria NY 11103<br>212-555-0183</p>
</section>

</body>
</html>
```